We need UI/UX design for a public, informational website for The Copper Lantern.
The pages, structure, and content scope are already defined. Designers are required to work only on the UI/UX layout of these existing pages, focusing on clarity, hierarchy, spacing, and usability. Do not add, remove, rename, or reinterpret pages or content.
The website is strictly informational only. It must not include accounts, onboarding, payments, custody, escrow administration, marketplaces, dashboards, or any transactional functionality.
Scope of work
Apply UI/UX design to the predefined website pages
Design layout for text, images, notices, and sections
Ensure consistent components and layout patterns across page types
Optimize layouts for long form, compliance focused content
Content writing, page creation, and branding changes are out of scope.
Structure reference
The complete page list, hierarchy, and content definitions are provided in the technical documentation and must be treated as the primary source of truth.
A Figma link is provided only as a light visual reference for page existence and structure:
https://meadow-knot-48203956.plumsite.example/
Designers must rely on the documentation for in depth and authoritative reference.
Brand guidelines
The Copper Lantern has existing brand guidelines and official logos, including light and dark versions. These assets will be provided and must be followed exactly. Designers must not redesign, alter, or reinterpret the brand identity.
Look and feel direction
The desired visual direction is inspired by:
https://ledgerwaltz.example/
This reference is provided only to indicate:
Institutional and enterprise tone
Clean, modern typography
Strong hierarchy and generous whitespace
Editorial, content first layouts
Do not copy branding, layouts, components, or assets from the reference site.
Hero section direction
The hero section should follow a similar structural approach to the hero used on https://ledgerwaltz.example/
, meaning:
Strong editorial framing
Clear headline hierarchy
Calm, institutional first impression
However, the background video must be Abu Dhabi focused, not generic or global. The video should visually reflect:
Abu Dhabi skyline or architectural language
Institutional, sovereign, long term infrastructure tone
Clean, slow, cinematic motion
No promotional, marketing, or lifestyle visuals
The hero must remain informational, restrained, and credible. No hype. No calls to invest. No implied participation.
Constraints
One global primary CTA only: “Continue to Halvemark” (external)
All other interactions must be informational
No visuals or language implying offers, investment, eligibility, or participation
Clear separation between informational content and any external operational platforms
Deliverables
High fidelity UI/UX designs created in Figma, covering:
Desktop layouts
Tablet layouts where relevant
Mobile layouts
Complete Figma file(s) including:
All designed pages defined in the technical documentation
A reusable component library (headers, footers, cards, notice panels, forms, CTAs, typography styles, spacing system)
Clearly defined layout grids, spacing rules, and text styles
Proper use of components and variants, not detached frames
Designs prepared for developer handoff, including:
Clear layer naming and structure
Auto layout where appropriate
Consistent use of styles and components
Responsive behavior demonstrated within Figma
Notes or annotations only where necessary for clarity
No prototypes, interactions, or motion design beyond basic layout states, unless explicitly requested. The focus is static UI/UX clarity, not animation.
A detailed technical specification document and official brand assets will be provided.
Any designs delivered outside Figma, that alter structure or content, or that ignore the defined constraints, boundaries, or tone will be rejected.

```html
<!DOCTYPE html>
<html lang="en">
<head>
<meta charset="utf-8">
<title>The Copper Lantern</title>
<link href="https://fonts.googleapis.com/css2?family=Bricolage+Grotesque:wght@300;400;800&family=Inter:wght@400;500;600&display=swap" rel="stylesheet">
<style>
:root{
  --blue:#5aa8f6;
  --violet:#a27cf6;
  --ink:#111418;
  --body:#5b5f66;
  --navy:#0f1b33;
  --white:#ffffff;
  --link:#3b9ae8;
  --accent:#6d8df0;
  --grad:linear-gradient(90deg,var(--blue),var(--violet));
}
*{box-sizing:border-box;margin:0;padding:0}
html,body{width:1200px;height:4098px;overflow:hidden}
body{position:relative;background:var(--white);font-family:"Inter",sans-serif;color:var(--ink)}
.abs{position:absolute}
.display{font-family:"Bricolage Grotesque",sans-serif;font-weight:300;letter-spacing:-.5px}
.display b{font-weight:800}

/* header */
.site-header{left:0;top:0;width:1200px;height:83px;background:var(--white)}
.brand{display:flex;align-items:center;gap:9px}
.brand-dot{width:13px;height:13px;border-radius:50%;background:var(--accent);flex:none}
.brand-name{font-size:14px;font-weight:600;color:#1b2233;letter-spacing:.3px;white-space:nowrap}
.main-nav{left:310px;top:30px;display:flex;gap:23px;font-size:15px;color:#222}
.main-nav .active{color:var(--link)}
.pill{display:inline-flex;align-items:center;justify-content:center;gap:8px;border-radius:30px;font-size:15px;font-weight:600;color:var(--white);background:var(--grad);height:44px;padding:0 28px;white-space:nowrap}
.pill svg{width:14px;height:14px}
.header-cta{left:888px;top:19px}

/* hero */
.hero{left:0;top:83px;width:1200px;height:601px;background:linear-gradient(180deg,#a9b6c2 0%,#8d9aa6 30%,#c9c1ad 48%,#2f8fa0 60%,#1a5b78 80%,#0f3f5c 100%)}
.hero-welcome{right:646px;top:498px;text-align:right;color:var(--white);font-size:50px;line-height:64px;white-space:nowrap}
.hero-welcome b{font-size:46px}
.hero-copy{left:605px;top:480px;width:455px;color:var(--white);font-size:16.5px;line-height:27px}
.hero-actions{left:605px;top:592px;display:flex;align-items:center;gap:30px}
.text-link{display:inline-flex;align-items:center;gap:8px;color:var(--white);font-weight:600;font-size:16px}
.text-link svg{width:15px;height:15px}

/* feature rows */
.feature-title{font-size:36px;line-height:48px}
.feature-text{font-size:13.5px;line-height:24px;color:var(--body);text-align:justify}
.small-pill{height:44px;padding:0 30px;font-size:14px}

/* bands */
.band{left:0;width:1200px;background:linear-gradient(90deg,#5aa8f6 0%,#8c8ff6 60%,#a27cf6 100%);color:var(--white);text-align:center}
.band-title{font-size:36px}
.layer{width:300px;text-align:center}
.layer-icon{width:118px;height:118px;border:3px solid var(--white);border-radius:50%;margin:0 auto;position:relative;display:flex;align-items:center;justify-content:center}
.layer-icon::before{content:"";position:absolute;left:14px;top:6px;width:14px;height:14px;border-radius:50%;background:var(--white)}
.layer-icon svg{width:58px;height:58px}
.layer h3{font-weight:400;font-size:18px;margin-top:20px}
.layer p{font-size:13.5px;line-height:24px;margin-top:6px;opacity:.95}
.outline-btn{display:inline-flex;align-items:center;gap:8px;height:42px;padding:0 26px;border:1.5px solid var(--white);border-radius:30px;font-size:14.5px;font-weight:600;color:var(--white)}
.outline-btn.solid{background:var(--white);color:var(--link)}
.outline-btn svg{width:13px;height:13px}

/* footer */
.site-footer{left:0;top:3742px;width:1200px;height:356px;background:var(--navy);color:var(--white)}
.footer-brand{display:flex;align-items:center;gap:10px}
.footer-brand .brand-dot{width:16px;height:16px}
.footer-name{font-size:17px;font-weight:500;letter-spacing:.4px;white-space:nowrap}
.social{display:flex;gap:9px}
.social span{width:28px;height:28px;border:1.5px solid var(--white);border-radius:50%}
.social span.on{background:var(--accent);border-color:var(--accent)}
.foot-col h4{font-size:15px;font-weight:500;letter-spacing:.3px;margin-bottom:10px}
.foot-col li{list-style:none;font-size:13.5px;line-height:24px;display:flex;gap:14px}
.foot-col li::before{content:"»";color:var(--accent)}
.foot-col li.cont::before{visibility:hidden}
.contact-item{display:flex;gap:12px;align-items:flex-start;font-size:13.5px;line-height:21px;margin-bottom:17px}
.contact-item i{width:24px;height:24px;border-radius:50%;background:var(--accent);flex:none;display:flex;align-items:center;justify-content:center}
.contact-item svg{width:12px;height:12px}
.copyright{left:0;top:4064px;width:1200px;text-align:center;font-size:13.5px;color:var(--white)}
</style>
</head>
<body>

<header class="abs site-header">
  <div class="abs brand" style="left:104px;top:32px"><span class="brand-dot"></span><span class="brand-name">THE COPPER LANTERN</span></div>
  <nav class="abs main-nav">
    <span class="active">Home</span><span>Framework</span><span>Projects</span><span>Halvemark</span><span>Insights</span><span>Company</span><span>Contact</span>
  </nav>
  <a class="abs pill header-cta">Continue to Halvemark</a>
</header>

<section class="abs hero" role="img" aria-label="Aerial photograph of the Abu Dhabi skyline and corniche beside the sea"></section>
<h1 class="abs display hero-welcome">Welcome To<br><b>The Copper Lantern</b></h1>
<p class="abs hero-copy">Its purpose is to define structural standards and oversight principles for complex initiatives that may involve multiple parties, staged execution, &amp; longterm accountability.</p>
<div class="abs hero-actions">
  <a class="pill" style="height:48px;padding:0 34px">Learn the Framework <svg viewBox="0 0 16 16"><circle cx="8" cy="8" r="8" fill="#fff"/><path d="M6.5 4.5 10 8l-3.5 3.5" stroke="#8c8ff6" stroke-width="2" fill="none"/></svg></a>
  <a class="text-link">Contact The Team <svg viewBox="0 0 16 16"><circle cx="8" cy="8" r="8" fill="#fff"/><path d="M6.5 4.5 10 8l-3.5 3.5" stroke="#1a5b78" stroke-width="2" fill="none"/></svg></a>
</div>

<!-- governance -->
<h2 class="abs display feature-title" style="left:143px;top:790px;width:420px">Governance <b>and Project Origination</b></h2>
<p class="abs feature-text" style="left:143px;top:912px;width:413px">Governance in this context refers to the standards that determine how projects are structured and how oversight is described. Origination refers to the initial design and definition of an initiative, including role separation, reporting expectations, and boundary setting before execution begins. The Copper Lantern focuses on these governance-level elements rather than on operating day-to-day workflows.</p>
<a class="abs pill small-pill" style="left:143px;top:1119px">Learn More <svg viewBox="0 0 16 16"><circle cx="8" cy="8" r="8" fill="#fff"/><path d="M6.5 4.5 10 8l-3.5 3.5" stroke="#8c8ff6" stroke-width="2" fill="none"/></svg></a>
<div class="abs" style="left:598px;top:760px;width:602px;height:441px;border-radius:4px 0 0 4px;background:linear-gradient(135deg,#d7dde3,#8894a2)" role="img" aria-label="Group of business professionals looking upward among city towers"></div>

<!-- role separation -->
<div class="abs" style="left:0;top:1279px;width:598px;height:441px;background:linear-gradient(135deg,#cfc9c0,#6e6a66)" role="img" aria-label="Team meeting around a table in a bright office"></div>
<h2 class="abs display feature-title" style="left:643px;top:1308px"><b>Clear Role</b> Separation</h2>
<p class="abs feature-text" style="left:643px;top:1382px;width:413px">The ecosystem is designed around clear separation of responsibilities. Governance activities belong at the framework layer. Operational workflows, where available, belong on a separate operating platform designed for process execution and recordkeeping. Assets and project execution, where applicable, belong at the project level through ring-fenced structures created for specific initiatives. This separation is intended to reduce ambiguity and help stakeholders understand who is responsible for what.</p>
<a class="abs pill small-pill" style="left:643px;top:1637px">Learn More <svg viewBox="0 0 16 16"><circle cx="8" cy="8" r="8" fill="#fff"/><path d="M6.5 4.5 10 8l-3.5 3.5" stroke="#8c8ff6" stroke-width="2" fill="none"/></svg></a>

<!-- ecosystem -->
<section class="abs band" style="top:1798px;height:520px">
  <h2 class="display band-title" style="margin-top:50px">How <b>the Ecosystem</b> Works</h2>
  <p style="font-size:17px;margin-top:8px">At a high level, the ecosystem can be understood as three layers:</p>
  <p style="font-size:13.5px;line-height:24px;width:860px;margin:16px auto 0">This website focuses on the governance layer and provides links to learn about structural concepts such as role separation, escrow and milestone framing, and recordkeeping terminology.</p>
  <div class="abs layer" style="left:135px;top:222px">
    <div class="layer-icon"><svg viewBox="0 0 60 60" fill="none" stroke="#fff" stroke-width="3"><path d="M6 38l12-10 10 6 12-8 14 12"/><path d="M20 44l10 8 10-8"/><circle cx="30" cy="16" r="8"/></svg></div>
    <h3>Governance</h3>
    <p>Defines standards, explains role boundaries, and publishes framework information</p>
  </div>
  <div class="abs layer" style="left:445px;top:222px">
    <div class="layer-icon"><svg viewBox="0 0 60 60" fill="none" stroke="#fff" stroke-width="3"><circle cx="22" cy="20" r="8"/><circle cx="40" cy="24" r="6"/><path d="M6 44h20l12-6c4-2 8 2 4 5L28 52H6"/></svg></div>
    <h3>Operations</h3>
    <p>Manages workflow processes such as documentation steps and record-anchored auditevents through a separate platform.</p>
  </div>
  <div class="abs layer" style="left:755px;top:222px">
    <div class="layer-icon"><svg viewBox="0 0 60 60" fill="none" stroke="#fff" stroke-width="3"><circle cx="30" cy="24" r="14"/><path d="M24 42h12M26 48h8"/><path d="M30 16v16M22 24h16"/></svg></div>
    <h3>Project Execution</h3>
    <p>Occurs at the project level through dedicated structures that hold responsibilities and assets where applicable.</p>
  </div>
</section>

<!-- escrow -->
<h2 class="abs display feature-title" style="left:143px;top:2426px;width:440px">Independent <b>Escrow and Milestone</b> Oversight</h2>
<p class="abs feature-text" style="left:143px;top:2550px;width:413px">Some initiatives use independent escrow arrangements to coordinate staged releases linked to milestone completion. Escrow can support execution discipline by requiring defined evidence before releases occur.Escrow does not guarantee outcomes, timelines, or success, and it is not administered by this website operator. This site describes the concept for clarity and transparency.</p>
<a class="abs pill small-pill" style="left:143px;top:2757px">Learn More <svg viewBox="0 0 16 16"><circle cx="8" cy="8" r="8" fill="#fff"/><path d="M6.5 4.5 10 8l-3.5 3.5" stroke="#8c8ff6" stroke-width="2" fill="none"/></svg></a>
<div class="abs" style="left:598px;top:2399px;width:602px;height:441px;border-radius:4px 0 0 4px;background:linear-gradient(135deg,#8fb6c6,#5d7d6a 55%,#c7c3b1)" role="img" aria-label="Aerial view of Abu Dhabi towers and coastline"></div>

<!-- operations -->
<div class="abs" style="left:0;top:2916px;width:598px;height:443px;background:linear-gradient(135deg,#e8e8e6,#9a9c96)" role="img" aria-label="Colleagues reviewing documents at an office table"></div>
<h2 class="abs display feature-title" style="left:643px;top:2973px;width:420px">Where <b>Operational</b> Workflows <b>Happen</b></h2>
<p class="abs feature-text" style="left:643px;top:3087px;width:413px">Operational workflows, including any onboarding or workflow participation where permitted, occur on a separate operating platform under separate terms &amp; policies. If you need operational access, use the Halvemark page on this site to navigate externally. This website does not host those workflows.</p>
<a class="abs pill small-pill" style="left:643px;top:3246px">Learn More <svg viewBox="0 0 16 16"><circle cx="8" cy="8" r="8" fill="#fff"/><path d="M6.5 4.5 10 8l-3.5 3.5" stroke="#8c8ff6" stroke-width="2" fill="none"/></svg></a>

<!-- contact -->
<section class="abs band" style="top:3437px;height:305px">
  <h2 class="display band-title" style="margin-top:52px">Contact <b>and Inquiries</b></h2>
  <p style="font-size:15px;line-height:26px;width:900px;margin:14px auto 0">If you have questions about governance framework concepts, role boundaries, or information published on this website, you can contact the team using the Contact page. Do not submit sensitive personal data through public forms</p>
  <div style="display:flex;justify-content:center;gap:14px;margin-top:32px">
    <a class="outline-btn">Learn the Framework <svg viewBox="0 0 16 16"><circle cx="8" cy="8" r="8" fill="#fff"/><path d="M6.5 4.5 10 8l-3.5 3.5" stroke="#8c8ff6" stroke-width="2" fill="none"/></svg></a>
    <a class="outline-btn solid">Continue to Halvemark <svg viewBox="0 0 16 16"><circle cx="8" cy="8" r="8" fill="#5aa8f6"/><path d="M6.5 4.5 10 8l-3.5 3.5" stroke="#fff" stroke-width="2" fill="none"/></svg></a>
    <a class="outline-btn">Contact the Team <svg viewBox="0 0 16 16"><circle cx="8" cy="8" r="8" fill="#fff"/><path d="M6.5 4.5 10 8l-3.5 3.5" stroke="#a27cf6" stroke-width="2" fill="none"/></svg></a>
  </div>
</section>

<footer class="abs site-footer">
  <div class="abs footer-brand" style="left:145px;top:98px"><span class="brand-dot"></span><span class="footer-name">THE COPPER LANTERN</span></div>
  <div class="abs social" style="left:172px;top:149px"><span class="on"></span><span></span><span></span><span></span></div>
  <div class="abs foot-col" style="left:407px;top:64px">
    <h4>NAVIGATION</h4>
    <ul><li>Framework</li><li>Projects</li><li>Halvemark</li><li>Insights</li><li>Company</li><li>Contact</li><li>Legal</li></ul>
  </div>
  <div class="abs foot-col" style="left:571px;top:64px">
    <h4>OTHER LINKS</h4>
    <ul><li>Legal</li><li>Terms of Use</li><li>Privacy Policy</li><li>Cookie Policy</li><li>Disclaimer &amp; Risk Notices</li><li>Acceptable Use Policy</li><li>Accessibility Statement</li><li class="cont">Glossary</li></ul>
  </div>
  <div class="abs foot-col" style="left:832px;top:64px">
    <h4 style="margin-bottom:16px">CONTACT US</h4>
    <div class="contact-item"><i><svg viewBox="0 0 12 12"><path d="M2 1h3l1 3-2 1a6 6 0 0 0 3 3l1-2 3 1v3c-6 0-9-3-9-9z" fill="#fff"/></svg></i><span style="padding-top:2px">+1-555-014-2871</span></div>
    <div class="contact-item"><i><svg viewBox="0 0 12 12"><rect x="1" y="2.5" width="10" height="7" fill="#fff"/><path d="M1 3l5 3.5L11 3" stroke="#6d8df0" fill="none"/></svg></i><span style="padding-top:2px">info@copperlantern.example</span></div>
    <div class="contact-item"><i><svg viewBox="0 0 12 12"><path d="M6 11S2 7 2 4.5a4 4 0 0 1 8 0C10 7 6 11 6 11z" fill="#fff"/><circle cx="6" cy="4.5" r="1.4" fill="#6d8df0"/></svg></i><span>48 Harbor Terrace, Suite 210<br>Eastvale 40318</span></div>
  </div>
</footer>
<p class="abs copyright">2026 Copyright - The Copper Lantern | All Rights Reserved</p>

</body>
</html>
```